Venture Capital Investment Firm

We are looking to overhaul our existing website (substantially), with only using the same logos (which we can provide).
We are an investment firm that focuses on making loans to late stage technology companies. Our site should ultimately look like other venture capital firms, and look modern and fresh. We have an existing website www.norvellhub.com which this will be replacing, although we will be using a lot of the existing written content, and potentially the numbers of pages we will need, we are not wed to anything else. Please feel free to shoot any questions at any time and thank you in advance for your help!
Websites we like as examples:
https://www.tesmarkfund.com/
https://www.brindlewoodpartners.com/
Target Market(s)
Potential investors who will invest in our firm, as well as potentially companies that are looking to borrow money from us.
Coding
Coded - Design and coding required
Number of Pages Required
5+ page
Colors
Designer to choose colors to be used in the design.
Look and feel

```html
<!DOCTYPE html>
<html lang="en">
<head>
<meta charset="utf-8">
<title>Norvell Hub Partners</title>
<link href="https://fonts.googleapis.com/css2?family=Cinzel:wght@700&family=Montserrat:wght@300;400&display=swap" rel="stylesheet">
<style>
:root{
  --navy:#0a0a3c;
  --royal:#00009c;
  --field:#1f1fae;
  --band:#f4f4f5;
  --line:#e2e2e6;
  --text:#333;
  --muted:#666;
  --white:#fff;
}
*{box-sizing:border-box;margin:0;padding:0}
html,body{width:883px;height:1200px;overflow:hidden;background:var(--white)}
body{position:relative;font-family:"Montserrat",sans-serif;color:var(--text)}
.abs{position:absolute}
.serif{font-family:"Cinzel",serif;font-weight:700}

.brand{left:57px;top:92px;display:flex;align-items:center;gap:14px;color:var(--navy)}
.brand-dot{width:52px;height:52px;border-radius:50%;background:var(--navy)}
.brand-name{font-size:62px;line-height:1;letter-spacing:1px}
.tagline{left:58px;top:212px;width:430px;font-size:17.5px;line-height:24.5px;color:#333}
.exp-label{left:58px;top:314px;font-size:11.5px;color:var(--navy);letter-spacing:.3px}
.stat{top:338px;text-align:center}
.stat b{display:block;font-family:"Cinzel",serif;font-size:28px;color:var(--navy);line-height:38px}
.stat span{display:block;font-size:10.5px;line-height:20px;color:var(--muted);font-weight:300}

.tiles{left:566px;top:48px;width:260px;height:421px;display:grid;grid-template-columns:130px 130px;grid-template-rows:138px 138px 145px;background:var(--band);border:1px solid var(--line)}
.tile{border-right:1px solid var(--line);border-bottom:1px solid var(--line);display:flex;flex-direction:column;align-items:center;justify-content:flex-end;padding-bottom:28px;text-align:center;font-size:11.5px;line-height:21px;color:var(--navy)}
.tile:nth-child(2n){border-right:none}
.tile:nth-child(n+5){border-bottom:none;padding-bottom:46px}
.tile svg{width:42px;height:42px;margin-bottom:8px;stroke:var(--navy);fill:none;stroke-width:1.6;stroke-linecap:round;stroke-linejoin:round}

.band{left:0;top:534px;width:883px;height:367px;background:var(--band)}
.band h2{position:absolute;top:54px;width:100%;text-align:center;font-size:28px;color:var(--navy);letter-spacing:.5px}
.avatar{left:56px;top:126px;width:117px;height:117px;border-radius:50%;border:2px solid var(--navy);background:radial-gradient(circle at 50% 45%,#c99a7c,#8a6a58 70%,#5d4a40)}
.quote{left:206px;top:130px;width:610px;font-size:11px;line-height:20px;color:var(--muted);font-weight:300}
.sig{left:206px;top:205px;font-size:15px;color:var(--navy)}
.dots{left:389px;top:278px;display:flex;gap:11px}
.dots i{width:12px;height:12px;border-radius:50%;border:1.5px solid var(--royal)}
.dots i:first-child{background:var(--royal)}

.footer{left:0;top:901px;width:883px;height:253px;background:var(--royal);color:var(--white)}
.f-brand{left:72px;top:88px;display:flex;align-items:center;gap:9px}
.f-dot{width:30px;height:30px;border-radius:50%;background:var(--white)}
.f-name{font-size:22px;line-height:1}
.legal{left:0;width:352px;top:140px;text-align:center;font-size:11.5px;text-decoration:underline}
.footer h3{position:absolute;top:25px;font-size:14.5px;letter-spacing:.3px}
.c-row{left:320px;display:flex;gap:21px;font-size:10.5px;line-height:20px;font-weight:300;letter-spacing:.3px}
.c-row svg{width:15px;height:18px;fill:var(--white);flex:none;margin-top:2px}
.news-text{left:583px;top:56px;width:245px;font-size:10.5px;line-height:20px;font-weight:300}
.field{left:582px;width:237px;height:35px;background:var(--field);font-size:10.5px;padding:11px 11px;font-weight:300}
.btn{left:582px;top:185px;width:118px;height:38px;border-radius:19px;background:var(--white);color:var(--navy);font-size:13px;text-align:center;line-height:38px}
.bottom{left:0;top:1154px;width:883px;height:46px;background:var(--band);text-align:center;line-height:46px;font-size:11px;color:#555}
</style>
</head>
<body>

<div class="abs brand serif"><span class="brand-dot"></span><span class="brand-name">NORVELL</span></div>
<p class="abs tagline">We take a different approach to providing growth capital with structured credit solutions for proven innovators in technology</p>
<p class="abs exp-label">OUR EXPERIENCE</p>
<div class="abs stat" style="left:62px;width:115px"><b>$1.2B</b><span>Over $1.2B invested<br>by our partners</span></div>
<div class="abs stat" style="left:188px;width:142px"><b>40+</b><span>40 Life science and<br>technology investments</span></div>
<div class="abs stat" style="left:348px;width:142px"><b>12+</b><span>Over a decade innovating<br>financing structures</span></div>

<nav class="abs tiles">
  <div class="tile"><svg viewBox="0 0 42 42"><path d="M21 5a10 10 0 0 0-6 18v5h12v-5a10 10 0 0 0-6-18z"/><path d="M21 5v23M16 32h10M17 36h8"/></svg>WE STARTED<br>WITH A BIG IDEA</div>
  <div class="tile"><svg viewBox="0 0 42 42"><circle cx="15" cy="24" r="5"/><circle cx="15" cy="24" r="9" stroke-dasharray="3 2.5"/><circle cx="30" cy="12" r="3"/><circle cx="30" cy="12" r="6" stroke-dasharray="2.5 2"/><circle cx="32" cy="28" r="2"/><circle cx="32" cy="28" r="4.5" stroke-dasharray="2 2"/></svg>WHAT WE LOOK<br>FOR</div>
  <div class="tile"><svg viewBox="0 0 42 42"><circle cx="21" cy="14" r="6"/><path d="M10 34c0-7 5-11 11-11s11 4 11 11z"/><circle cx="11" cy="16" r="4.5"/><circle cx="31" cy="16" r="4.5"/><path d="M4 31c0-5 3-8 7-8M38 31c0-5-3-8-7-8"/></svg>OUR TEAM</div>
  <div class="tile"><svg viewBox="0 0 42 42"><circle cx="21" cy="17" r="12"/><circle cx="21" cy="17" r="8"/><path d="M17 17l3 3 5-6M14 27l-3 12 5-3 3 4 2-10M28 27l3 12-5-3-3 4-2-10"/></svg>OUR VALUES</div>
  <div class="tile"><svg viewBox="0 0 42 42"><circle cx="21" cy="10" r="7"/><path d="M21 6v8M19 8h3a1.5 1.5 0 0 1 0 3h-2a1.5 1.5 0 0 0 0 3h3M21 17v8M21 24c-3-3-7-3-8-1M21 24c3-3 7-3 8-1M4 30h8l6 3h8l10-6c2 0 2 3 0 4l-12 7H12l-8-2"/></svg>OUR INVESTMENTS</div>
  <div class="tile"><svg viewBox="0 0 42 42"><rect x="6" y="8" width="32" height="27"/><path d="M3 14v21h3M11 14h22M11 20h22M11 25h22M11 30h22"/></svg>NEWS</div>
</nav>

<section class="abs band">
  <h2 class="serif">WHAT OUR PARTNERS SAY</h2>
  <div class="abs avatar" role="img" aria-label="Portrait photo of a partner"></div>
  <p class="abs quote">Lorem Ipsum is simply dummy text of the printing and typesetting industry. Lorem Ipsum has been the industry's standard dummy text ever since the 1500s, when an unknown printer took a galley of type and scrambled it to make a type specimen book.</p>
  <p class="abs sig serif">CEO - PARTNER NAME</p>
  <div class="abs dots"><i></i><i></i><i></i><i></i><i></i></div>
</section>

<footer class="abs footer">
  <div class="abs f-brand serif"><span class="f-dot"></span><span class="f-name">NORVELL HUB</span></div>
  <p class="abs legal">Legal Disclaimer</p>

  <h3 class="serif" style="left:320px">CONTACT US</h3>
  <div class="abs c-row" style="top:56px"><svg viewBox="0 0 15 20"><path d="M7.5 0A7 7 0 0 0 .5 7c0 5 7 13 7 13s7-8 7-13a7 7 0 0 0-7-7zm0 10a3 3 0 1 1 0-6 3 3 0 0 1 0 6z"/></svg><span>SAN FRANCISCO<br>2250 Harlow Avenue #318<br>San Francisco, CA &nbsp;94110</span></div>
  <div class="abs c-row" style="top:145px"><svg viewBox="0 0 16 12"><path d="M0 0h16v2L8 7 0 2zM0 4l8 5 8-5v8H0z"/></svg><span>GENERAL INQUIRIES : :<br>inquiries@norvellhub.com</span></div>
  <div class="abs c-row" style="top:197px"><svg viewBox="0 0 16 12"><path d="M0 0h16v2L8 7 0 2zM0 4l8 5 8-5v8H0z"/></svg><span>MEDIA INQUIRIES :<br>media@norvellhub.com</span></div>

  <h3 class="serif" style="left:583px">NEWSLETTER</h3>
  <p class="abs news-text">Would you like to receive our exclusive news and update for signup our newsletter !</p>
  <div class="abs field" style="top:103px">Enter Name *</div>
  <div class="abs field" style="top:140px">Enter Email *</div>
  <div class="abs btn serif">SUBSCRIBE</div>
</footer>

<div class="abs bottom">©2019 Norvell Hub Partners LLC. &nbsp;All Rights Reserved.</div>

</body>
</html>
```